Now Leasing Banner

Looking for a banner that says the following information approx 4' x 30'

Now Leasing Maplebrook Terrace 925-318-6042

Target Market(s)

Drive by traffic

Industry/Entity Type

Residential property management

Requirements
Must have
• Clear and readable from a distance

```html
<!DOCTYPE html>
<html lang="en">
<head>
<meta charset="utf-8">
<title>Maplebrook Terrace – Now Leasing Banner</title>
<link rel="stylesheet" href="https://fonts.googleapis.com/css2?family=Josefin+Sans:wght@600;700&display=swap">
<style>
  :root {
    --page-bg: #d9d8da;
    --banner-bg: #ffffff;
    --ink-blue: #2e3192;
    --ink-shadow: #b9b9bd;
    --photo-sky: #eef0f3;
    --photo-building: #b9c0c9;
    --photo-shade: #8f97a3;
  }
  html, body {
    margin: 0;
    padding: 0;
    width: 1200px;
    height: 662px;
    overflow: hidden;
    background: var(--page-bg);
  }
  .canvas {
    position: relative;
    width: 1200px;
    height: 662px;
  }
  .banner {
    position: absolute;
    left: 30px;
    top: 255px;
    width: 1140px;
    height: 152px;
    background: var(--banner-bg);
    box-shadow: 10px 12px 14px rgba(0, 0, 0, 0.28);
    overflow: hidden;
  }
  .banner__photo {
    position: absolute;
    left: 0;
    top: 0;
    width: 230px;
    height: 152px;
    background:
      linear-gradient(90deg, rgba(255,255,255,0) 0%, rgba(255,255,255,0) 62%, var(--banner-bg) 100%),
      linear-gradient(180deg, var(--photo-sky) 0%, var(--photo-building) 45%, var(--photo-shade) 100%);
  }
  .banner__copy {
    position: absolute;
    left: 0;
    top: 0;
    width: 1140px;
    height: 152px;
  }
  .banner__copy text {
    font-family: "Josefin Sans", sans-serif;
    font-weight: 700;
    text-transform: uppercase;
  }
  .copy--shadow { fill: var(--ink-shadow); }
  .copy--ink { fill: var(--ink-blue); }
</style>
</head>
<body>
<main class="canvas">
  <section class="banner">
    <div class="banner__photo" role="img" aria-label="Photo of a hand holding a house-shaped key ring in front of a blurred apartment building"></div>
    <svg class="banner__copy" viewBox="0 0 1140 152" xmlns="http://www.w3.org/2000/svg">
      <g class="copy--shadow" aria-hidden="true">
        <text x="243" y="100" font-size="92" textLength="870" lengthAdjust="spacingAndGlyphs">Maplebrook Terrace</text>
        <text x="243" y="142" font-size="45" textLength="870" lengthAdjust="spacingAndGlyphs">Now Leasing 925-318-6042</text>
      </g>
      <g class="copy--ink">
        <text class="banner__headline" x="240" y="97" font-size="92" textLength="870" lengthAdjust="spacingAndGlyphs">Maplebrook Terrace</text>
        <text class="banner__tagline" x="240" y="139" font-size="45" textLength="870" lengthAdjust="spacingAndGlyphs">Now Leasing 925-318-6042</text>
      </g>
    </svg>
  </section>
</main>
</body>
</html>
```